Lantern Petals Website v.1 - attract floral shop franchisees

I need a simple information website for my new business. We are a franchisor of flower shops. The overall purpose of the website is to promote the company and the service, especially to potential franchisees and retailers. Only about 4 pages are required including homepage, About, For Supermarkets, For Franchisees, and Contact. No special functions are required except the site will have two separate inquiry forms that must be filled out online and submitted via automated email. Similarly, an email form should be linked from the Contact page. I have a logo and business cards designed by ArtMingle, and I would like the site to have a consistent color scheme and style. The key to design will be to express the joy and love associated with flowers and floral bouquets.
IMPORTANT - I will be exporting the website design to Wordpress CMS in a site hosted by HostNimbus. For smooth integration into WordPress hosted by HostNimbus, the designer should build the site using a WordPress-friendly format. Ideally, they should use HTML, CSS, and PHP. Creating a custom theme or using a page builder that exports to WordPress-compatible files is best. This ensures the site can be easily imported and managed within WordPress.

Target Market(s)

Potential franchisees (existing florists or creative types who might like to own a floral business) and supermarkets who might want us to run their floral department

Industry/Entity Type

Floral retailing

Requirements
Must have
• A brand theme that is beautiful, consistent throughout and builds on the logo design
Nice to have
• Show gender and ethnic diversity in customers and florists. Pictures of happy florists (for franchisees) and pictures of amazing floral department displays (for supermarkets)

```html
<!DOCTYPE html>
<html lang="en">
<head>
<meta charset="utf-8">
<title>Lantern Petals – Floral Franchising</title>
<link href="https://fonts.googleapis.com/css2?family=Dancing+Script:wght@700&family=Inter:wght@400;500;600;700&display=swap" rel="stylesheet">
<style>
:root{
  --green:#14914b;
  --green-dark:#0c8a43;
  --orange:#ef9f24;
  --orange-deep:#e8951c;
  --ink:#1d1d1d;
  --white:#ffffff;
  --black:#000000;
  --hero-a:#cfd3d6;
  --hero-b:#8f9699;
}
*{box-sizing:border-box;margin:0;padding:0}
html,body{width:1200px;height:3528px;overflow:hidden;background:var(--white)}
body{position:relative;font-family:"Inter",Arial,sans-serif;color:var(--ink)}
.abs{position:absolute}
.script{font-family:"Dancing Script",cursive;font-weight:700}
.nowrap{white-space:nowrap}
.btn{position:absolute;display:flex;align-items:center;justify-content:center;border-radius:24px;font-family:"Dancing Script",cursive;font-weight:700;font-size:20px;text-decoration:none;white-space:nowrap}
.btn-green{background:var(--green);color:var(--white)}
.btn-white{background:var(--white);color:var(--green)}

/* header */
.site-header{position:absolute;left:0;top:0;width:1200px;height:90px;background:var(--white);border-top:4px solid var(--orange);box-shadow:0 2px 6px rgba(0,0,0,.08);z-index:3}
.brand{position:absolute;left:100px;top:28px;display:flex;align-items:center;gap:10px}
.brand-dot{width:26px;height:26px;border-radius:50%;background:var(--orange)}
.brand-name{font-size:22px;font-weight:600;color:var(--green)}
.main-nav a{position:absolute;top:34px;font-size:15px;color:var(--ink);text-decoration:none}

/* hero */
.hero{position:absolute;left:0;top:90px;width:1200px;height:660px;overflow:hidden}
.hero-photo{position:absolute;inset:0;background:linear-gradient(100deg,#f0d6d3 0%,#d9dcd8 30%,var(--hero-a) 50%,var(--hero-b) 100%)}
.hero-title{position:absolute;left:680px;top:130px;font-size:72px;color:var(--white);white-space:nowrap}
.hero-text{position:absolute;left:680px;top:221px;width:480px;font-size:13.5px;line-height:31px;color:var(--white);white-space:nowrap}

/* about */
.about-title{left:98px;top:778px;font-size:44px;color:var(--orange)}
.body-text{font-size:13.5px;line-height:31px;color:var(--ink);white-space:nowrap}
.about-photo{left:655px;top:803px;width:414px;height:414px;border-radius:50%;border:10px solid var(--orange);padding:10px;background:var(--white)}
.about-photo div{width:100%;height:100%;border-radius:50%;background:radial-gradient(circle at 50% 40%,#e34c8d 0%,#d8477f 35%,#7c9a5c 70%,#bfbfbf 100%)}

/* supermarkets */
.markets{position:absolute;left:0;top:1330px;width:1200px;height:727px;background:var(--green)}
.markets-title{left:0;width:1200px;text-align:center;top:62px;font-size:44px;color:var(--white)}
.markets-text{left:0;width:1200px;top:128px;text-align:center;font-size:13.5px;line-height:31px;color:var(--white);white-space:nowrap}
.round-photo{position:absolute;border-radius:50%;border:5px solid var(--white)}
.opp-title{left:621px;top:248px;font-size:21px;font-weight:500;color:var(--white)}
.opp-list{left:621px;top:282px;width:520px;list-style:none;font-size:13.5px;line-height:34.3px;color:var(--white);white-space:nowrap}
.opp-list li::before{content:"";display:inline-block;width:11px;height:11px;border-radius:50%;background:var(--white);margin-right:4px;vertical-align:-1px}

/* franchisees */
.fr-title{left:100px;top:2152px;font-size:44px;color:var(--ink)}

/* cta */
.cta{position:absolute;left:0;top:2657px;width:1200px;height:430px;background:linear-gradient(180deg,#f2a52b,var(--orange-deep))}
.cta-text{left:0;width:1200px;top:62px;text-align:center;font-size:31px;line-height:40px;color:var(--white);white-space:nowrap}

/* footer */
.footer{position:absolute;left:0;top:3060px;width:1200px;height:468px;background:var(--black);color:var(--white)}
.foot-brand{position:absolute;left:100px;top:170px;display:flex;align-items:center;gap:14px}
.foot-brand .brand-dot{width:40px;height:40px}
.foot-brand .brand-name{font-size:34px;color:var(--orange)}
.foot-col{position:absolute;top:92px;white-space:nowrap}
.foot-col h4{font-size:15px;font-weight:700;margin-bottom:20px}
.foot-col p{font-size:13px;line-height:40px}
.social{position:absolute;top:338px;width:32px;height:32px;border-radius:3px}
.copyright{position:absolute;left:0;width:1200px;top:393px;text-align:center;font-size:14px}
</style>
</head>
<body>

<header class="site-header">
  <div class="brand"><span class="brand-dot"></span><span class="brand-name">Lantern Petals</span></div>
  <nav class="main-nav">
    <a style="left:578px" href="#">About Us</a>
    <a style="left:700px" href="#">For Supermarkets</a>
    <a style="left:881px" href="#">For Franchisees</a>
    <a style="left:1040px" href="#">Contact</a>
  </nav>
</header>

<section class="hero">
  <div class="hero-photo" role="img" aria-label="Soft pink and white rose bouquet resting on a car bonnet"></div>
  <h1 class="hero-title script">Lantern Petals</h1>
  <p class="hero-text">Fresh flowers convey beauty and love, and in our view<br>should become something every person regularly enjoys.<br>Lantern Petals is an entrepreneurial company created to<br>make top quality fresh flowers</p>
  <a class="btn btn-green" style="left:680px;top:370px;width:141px;height:46px" href="#">Get Started</a>
</section>
<svg class="abs" style="left:0;top:590px" width="1200" height="170" viewBox="0 0 1200 170" aria-hidden="true">
  <path d="M0 160 C120 60 300 40 520 70 C720 100 860 150 1000 110 C1100 80 1160 40 1200 20 L1200 170 L0 170 Z" fill="#fff"/>
  <path d="M150 75 C350 35 560 70 760 110 C920 140 1060 110 1200 40 L1200 58 C1060 140 900 160 750 130 C560 95 360 60 150 75 Z" fill="var(--green)"/>
  <path d="M0 160 C120 60 300 40 520 70 C720 100 860 150 1000 110 C1100 80 1160 40 1200 12" fill="none" stroke="var(--orange)" stroke-width="5"/>
</svg>

<section class="about">
  <h2 class="abs about-title script">About Us</h2>
  <p class="abs body-text" style="left:98px;top:850px">Fresh flowers convey beauty and love, and in our view should become<br>something every person regularly enjoys.&nbsp; Lantern Petals is an<br>entrepreneurial company created to make top quality fresh flowers<br>and professionally-designed bouquets accessible to every consumer<br>at affordable prices.</p>
  <p class="abs body-text" style="left:98px;top:1035px">Professional florists typically sell the finest quality stems, design the<br>most beautiful bouquets and provide the finest customer service, but<br>their costs – of floral products, retail spaces, labor and marketing –<br>force them to pass high prices along to customers.</p>
  <a class="btn btn-green" style="left:98px;top:1183px;width:141px;height:46px" href="#">Read More</a>
  <div class="abs about-photo"><div role="img" aria-label="Pink hat box filled with roses and calla lilies"></div></div>
</section>

<section class="markets">
  <div class="abs" style="inset:0;background:radial-gradient(circle at 30% 40%,rgba(255,255,255,.08),transparent 60%)" role="img" aria-label="Faint green tinted flower backdrop"></div>
  <h2 class="abs markets-title script">Supermarkets</h2>
  <p class="abs markets-text">Lantern Petals works with some of the country's largest and most progressive supermarkets to provide franchisee ownership and<br>operation of their strategically important floral departments.&nbsp; Supermarkets find that Lantern Petals is able to improve their financial<br>outcomes, provide attentive customer service and satisfaction, and lift the quality of the entire store environment.</p>
  <div class="round-photo" style="left:212px;top:265px;width:352px;height:352px;background:radial-gradient(circle,#e83a3a 0%,#d9435a 45%,#e9a9a2 80%,#cfcfcf 100%)" role="img" aria-label="Bouquet of red and pink roses held in hands"></div>
  <div class="round-photo" style="left:105px;top:220px;width:190px;height:190px;background:linear-gradient(135deg,#6b6f55,#3d3d30 60%,#c9783a)" role="img" aria-label="Florist arranging flowers at a market stall"></div>
  <h3 class="abs opp-title">Opportunity for Supermarkets</h3>
  <ul class="abs opp-list">
    <li>Enhance floral revenue streams with efficient assortments and new<br>offerings</li>
    <li>Reduce the costs of operating a floral department</li>
    <li>Improve the quality, useful life and merchandising of floral products</li>
    <li>Provide attentive customer service, including semi-custom bouquets,<br>by professional florist staff</li>
    <li>Maintain a beautiful, fresh and well-stocked environment</li>
    <li>Increase sales and profits</li>
    <li>Enhance the entire customer shopping environment</li>
  </ul>
</section>

<section class="franchisees">
  <h2 class="abs fr-title script">Franchisees</h2>
  <p class="abs body-text" style="left:100px;top:2225px">Lantern Petals brings the best of professional florists and<br>supermarkets together for the benefit of consumers.&nbsp; It supports a<br>national network of owner-operator franchisees, who in many cases<br>are multi-site professional florists, with comprehensive services to<br>enhance franchise profitability.&nbsp; Lantern Petals works with some of<br>the country's largest and most progressive supermarkets to provide<br>franchisee ownership and operation of their strategically important<br>floral departments.</p>
  <a class="btn btn-green" style="left:100px;top:2497px;width:141px;height:46px" href="#">Read More</a>
  <div class="abs" style="left:843px;top:2162px;width:284px;height:243px;background:var(--green)"></div>
  <div class="abs" style="left:642px;top:2298px;width:30px;height:202px;background:var(--orange)"></div>
  <div class="abs" style="left:663px;top:2187px;width:438px;height:360px;background:linear-gradient(180deg,#8c8777 0%,#6f6a58 35%,#c8464a 70%,#e8c35a 100%)" role="img" aria-label="Smiling florist holding a potted plant in a garden centre"></div>
</section>

<section class="cta">
  <p class="abs cta-text script">Lorem ipsum dolor sit amet, consectetur adipiscing elit, sed do eiusmod<br>tempor incididunt ut labore et dolore magna aliqua.</p>
  <a class="btn btn-green" style="left:287px;top:171px;width:273px;height:49px" href="#">New Florist Franchise Inquiry</a>
  <a class="btn btn-white" style="left:579px;top:171px;width:334px;height:49px" href="#">Professional Florist Franchise Inquiry</a>
</section>

<footer class="footer">
  <div class="foot-brand"><span class="brand-dot"></span><span class="brand-name">Lantern Petals</span></div>
  <div class="foot-col" style="left:440px"><h4>COURSES</h4><p>Full Qualifications<br>High Risk Licencing<br>Plant Operator Tickets<br>Short Courses</p></div>
  <div class="foot-col" style="left:638px"><h4>STUDENT RESOURCES</h4><p>Enrolment Form<br>Student Handbook<br>Support<br>Contact us</p></div>
  <div class="foot-col" style="left:851px"><h4>CONTACT INFORMATION</h4><p>Marcus T. Hollin Founder and CEO<br>Phone : +1.555.204.7718<br>Mon – Fri 7:30am to 4:30pm<br>Email : marcus@lantern-petals.com</p></div>
  <span class="social" style="left:556px;background:#3b5998"></span>
  <span class="social" style="left:598px;background:#e1306c"></span>
  <span class="social" style="left:642px;background:#0e76a8"></span>
  <p class="copyright">© 2024 - Lantern-Petals – All Rights Reserved</p>
</footer>
<svg class="abs" style="left:0;top:2960px" width="1200" height="140" viewBox="0 0 1200 140" aria-hidden="true">
  <path d="M0 125 C150 40 330 0 520 30 C720 60 880 110 1020 80 C1110 60 1170 20 1200 0 L1200 140 L0 140 Z" fill="var(--black)"/>
  <path d="M0 108 C160 25 340 -5 540 28 C720 58 880 100 1030 70 C1110 50 1170 15 1200 -5 L1200 10 C1170 30 1110 68 1020 90 C870 120 720 80 530 50 C340 20 170 50 0 122 Z" fill="var(--green)"/>
  <path d="M0 125 C150 40 330 0 520 30 C720 60 880 110 1020 80 C1110 60 1170 20 1200 0" fill="none" stroke="var(--white)" stroke-width="4"/>
  <path d="M0 132 C150 50 330 12 520 42 C720 72 880 120 1020 92 C1110 72 1170 32 1200 12" fill="none" stroke="var(--orange)" stroke-width="4"/>
</svg>

</body>
</html>
```